Trailer wrap for home remodeling company in Sarasota County Florida

I need a wrap design for an enclosed trailer. I like the idea of adding a picture of a really nice kitchen or bathroom, possibly a before and after.
Matte black background
Must include the below information
Pinecrest Home Remodeling
CGC2871093
941-555–0184
www.pinecresthomeremodeling.example
Bathrooms,Kitchens, Additions, Remodels
Trusted Expertise. Refined Design
Trailer is currently all black
Updates

Designs are not what we are looking for, very busy

Industry/Entity Type

Home Remodeling

Colors
0054AA
0677BA
7BADD7
CADEEF
E8F1F8

Requirements
Must have
• Matte black background

```html
<!DOCTYPE html>
<html lang="en">
<head>
<meta charset="utf-8">
<title>Pinecrest Home Remodeling – Trailer Wrap</title>
<link rel="stylesheet" href="https://fonts.googleapis.com/css2?family=Barlow+Condensed:wght@500&family=Barlow+Semi+Condensed:wght@700&family=Poppins:wght@500;600&display=swap">
<style>
  :root{
    --matte:#0b0b0c;
    --charcoal:#2a2b2d;
    --navy:#0054AA;
    --blue:#0677BA;
    --sky:#7BADD7;
    --mist:#CADEEF;
    --frost:#E8F1F8;
    --bright:#1b8fdc;
    --phone:#d6d8db;
    --white:#ffffff;
    --stage:#eceef0;
  }
  *{box-sizing:border-box;margin:0;padding:0}
  html,body{width:1200px;height:2399px;overflow:hidden;background:var(--stage)}
  .wrap-sheet{position:relative;width:1200px;height:2399px}

  .side-panel{position:absolute;left:40px;width:1120px;height:560px;background:var(--matte);overflow:hidden}
  .side-panel svg{position:absolute;inset:0}
  .side-street{top:60px}
  .side-curb{top:720px}

  .info{position:absolute;top:0;width:560px;height:560px;color:var(--white)}
  .side-curb .info{left:30px}
  .side-street .info{left:560px}
  .side-street .info > *{left:auto;right:30px}

  .brand-name{font-family:"Poppins",sans-serif;font-weight:600;font-size:34px;line-height:1.1;position:absolute;top:56px;left:0;width:500px;color:var(--white)}
  .side-street .brand-name{text-align:right}

  .tagline{font-family:"Barlow Condensed",sans-serif;font-weight:500;font-size:34px;line-height:1;position:absolute;top:128px;left:0;width:500px;color:var(--white)}
  .side-street .tagline{text-align:right}

  .services{position:absolute;top:196px;left:0;width:500px;display:flex;align-items:center;gap:22px}
  .side-street .services{flex-direction:row-reverse}
  .license{font-family:"Poppins",sans-serif;font-weight:500;font-size:19px;color:#e3e3e3;background:var(--charcoal);padding:6px 18px;clip-path:polygon(0 0,100% 0,90% 100%,0 100%)}
  .service-list{list-style:none;display:grid;grid-template-columns:auto auto;gap:2px 28px;font-family:"Poppins",sans-serif;font-weight:600;font-size:20px;text-align:left}
  .service-list li::before{content:"";display:inline-block;width:7px;height:7px;border-radius:50%;background:var(--bright);margin-right:8px;vertical-align:middle}

  .phone{font-family:"Barlow Semi Condensed",sans-serif;font-weight:700;font-size:78px;line-height:1;color:var(--phone);position:absolute;top:312px;left:0;width:470px;letter-spacing:1px}
  .side-street .phone{text-align:right}
  .website{font-family:"Poppins",sans-serif;font-weight:500;font-size:21px;line-height:1;position:absolute;top:419px;left:0;width:460px}
  .side-street .website{text-align:right}

  .front-pair{position:absolute;top:1390px;left:0;width:1200px;display:flex;justify-content:center;gap:70px}
  .front-panel{width:320px;height:900px;background:var(--matte);color:var(--white);display:flex;flex-direction:column;align-items:center;padding:70px 24px 0;text-align:center}
  .front-name{font-family:"Poppins",sans-serif;font-weight:600;font-size:26px;line-height:1.2}
  .front-tag{font-family:"Barlow Condensed",sans-serif;font-weight:500;font-size:28px;line-height:1.1;margin-top:34px}
  .front-license{font-family:"Poppins",sans-serif;font-weight:500;font-size:16px;background:var(--charcoal);padding:6px 14px;margin-top:34px}
  .front-services{list-style:none;margin-top:34px;display:flex;flex-direction:column;gap:14px}
  .front-services li{font-family:"Poppins",sans-serif;font-weight:500;font-size:19px;background:var(--bright);width:160px;padding:4px 0}
  .front-phone{font-family:"Barlow Semi Condensed",sans-serif;font-weight:700;font-size:44px;color:var(--bright);margin-top:44px;line-height:1}
  .front-web{font-family:"Poppins",sans-serif;font-weight:500;font-size:12px;margin-top:8px}
</style>
</head>
<body>
<main class="wrap-sheet">

  <section class="side-panel side-street">
    <svg viewBox="0 0 1120 560" width="1120" height="560">
      <defs>
        <linearGradient id="kitchenA" x1="0" y1="0" x2="1" y2="1">
          <stop offset="0" stop-color="#e9ecef"/><stop offset=".55" stop-color="#c9cfd4"/><stop offset="1" stop-color="#f4f5f6"/>
        </linearGradient>
        <linearGradient id="bandA" x1="0" y1="0" x2="1" y2="0">
          <stop offset="0" stop-color="#0054AA"/><stop offset="1" stop-color="#0677BA"/>
        </linearGradient>
        <linearGradient id="footA" x1="0" y1="0" x2="1" y2="0">
          <stop offset="0" stop-color="#0677BA"/><stop offset="1" stop-color="#7BADD7"/>
        </linearGradient>
      </defs>
      <g transform="translate(1120,0) scale(-1,1)">
        <polygon points="0,300 560,300 530,400 0,400" fill="url(#bandA)"/>
        <polygon points="0,400 530,400 510,460 0,460" fill="#2a2b2d"/>
        <polygon points="0,460 510,460 480,560 0,560" fill="url(#footA)"/>
        <rect x="0" y="292" width="565" height="5" fill="#cfd3d6"/>
        <polygon role="img" aria-label="Photo of a bright modern white kitchen with open drawers" points="640,0 1120,0 1120,560 520,560" fill="url(#kitchenA)"/>
        <polygon points="585,60 625,60 505,420 465,420" fill="#0054AA"/>
        <polygon points="610,0 640,0 520,560 490,560" fill="#2a2b2d"/>
        <polygon points="700,200 760,200 620,560 560,560" fill="#7BADD7" opacity=".45"/>
        <polygon points="1120,380 1120,560 900,560" fill="#0677BA" opacity=".75"/>
      </g>
    </svg>
    <div class="info">
      <h1 class="brand-name">Pinecrest Home Remodeling</h1>
      <p class="tagline">Trusted Expertise. Refined Design</p>
      <div class="services">
        <span class="license">CGC2871093</span>
        <ul class="service-list"><li>Bathrooms</li><li>Additions</li><li>Kitchens</li><li>Remodels</li></ul>
      </div>
      <p class="phone">941-555–0184</p>
      <p class="website">www.pinecresthomeremodeling.example</p>
    </div>
  </section>

  <section class="side-panel side-curb">
    <svg viewBox="0 0 1120 560" width="1120" height="560">
      <defs>
        <linearGradient id="kitchenB" x1="1" y1="0" x2="0" y2="1">
          <stop offset="0" stop-color="#e9ecef"/><stop offset=".55" stop-color="#c9cfd4"/><stop offset="1" stop-color="#f4f5f6"/>
        </linearGradient>
      </defs>
      <polygon points="0,300 560,300 530,400 0,400" fill="url(#bandA)"/>
      <polygon points="0,400 530,400 510,460 0,460" fill="#2a2b2d"/>
      <polygon points="0,460 510,460 480,560 0,560" fill="url(#footA)"/>
      <rect x="0" y="292" width="565" height="5" fill="#cfd3d6"/>
      <polygon role="img" aria-label="Photo of a bright modern white kitchen with open drawers" points="640,0 1120,0 1120,560 520,560" fill="url(#kitchenB)"/>
      <polygon points="585,60 625,60 505,420 465,420" fill="#0054AA"/>
      <polygon points="610,0 640,0 520,560 490,560" fill="#2a2b2d"/>
      <polygon points="700,200 760,200 620,560 560,560" fill="#7BADD7" opacity=".45"/>
      <polygon points="1120,380 1120,560 900,560" fill="#0677BA" opacity=".75"/>
    </svg>
    <div class="info">
      <h2 class="brand-name">Pinecrest Home Remodeling</h2>
      <p class="tagline">Trusted Expertise. Refined Design</p>
      <div class="services">
        <span class="license">CGC2871093</span>
        <ul class="service-list"><li>Bathrooms</li><li>Additions</li><li>Kitchens</li><li>Remodels</li></ul>
      </div>
      <p class="phone">941-555–0184</p>
      <p class="website">www.pinecresthomeremodeling.example</p>
    </div>
  </section>

  <section class="front-pair">
    <article class="front-panel">
      <h3 class="front-name">Pinecrest Home<br>Remodeling</h3>
      <p class="front-tag">Trusted Expertise<br>Refined Design</p>
      <p class="front-license">License # CGC2871093</p>
      <ul class="front-services"><li>Bathrooms</li><li>Kitchens</li><li>Additions</li><li>Remodels</li></ul>
      <p class="front-phone">941-555–0184</p>
      <p class="front-web">www.pinecresthomeremodeling.example</p>
    </article>
    <article class="front-panel">
      <h3 class="front-name">Pinecrest Home<br>Remodeling</h3>
      <p class="front-tag">Trusted Expertise<br>Refined Design</p>
      <p class="front-license">License # CGC2871093</p>
      <ul class="front-services"><li>Bathrooms</li><li>Kitchens</li><li>Additions</li><li>Remodels</li></ul>
      <p class="front-phone">941-555–0184</p>
      <p class="front-web">www.pinecresthomeremodeling.example</p>
    </article>
  </section>

</main>
</body>
</html>
```